Automotive eCommerce Business looking for a business card design

Looking for a clean and simple business card design. Our company name is "Brindle Auto" and we are a company specializing in the ecommerce sales of automotive parts, specifically for pick up trucks and large SUVs. Our company colours are red, black, and white.

Feel free to use the logo provided or create a new logo that you seem fit. Looking forward to your creative ideas!

Industry/Entity Type

Automotive

Contact Information for Business Card

We were thinking of a possibly two-sided design featuring just the logo and company name on one side, and personal information on the other side. Single sided designs will be considered as well.

Font styles to use
Serif
Sans Serif
Decorative

Colors
ec1f27
ffffff
000000

Requirements
Must have
• Space for employee's name, title, phone number and email address, along with the company address and website somewhere.

```html
<!DOCTYPE html>
<html lang="en">
<head>
<meta charset="utf-8">
<title>Brindle Auto – Business Card</title>
<link href="https://fonts.googleapis.com/css2?family=Cinzel:wght@500&family=Roboto:wght@400;500;700&display=swap" rel="stylesheet">
<style>
  :root {
    --page-bg: #d9d6d2;
    --card-bg: #f1f0ee;
    --card-edge: #c9c7c4;
    --brand-red: #8c1b22;
    --ink: #2b2b2b;
    --ink-soft: #3a3a3a;
  }
  * { margin: 0; padding: 0; box-sizing: border-box; }
  html, body {
    width: 1200px;
    height: 969px;
    overflow: hidden;
    background: var(--page-bg);
  }
  .business-card {
    position: absolute;
    left: 100px;
    top: 199px;
    width: 1000px;
    height: 571px;
    background: var(--card-bg);
    border: 2px solid var(--card-edge);
    border-radius: 26px;
    overflow: hidden;
    font-family: "Roboto", Arial, sans-serif;
    color: var(--ink);
  }
  .company-name {
    position: absolute;
    left: 62px;
    top: 72px;
    font-family: "Cinzel", Georgia, serif;
    font-weight: 500;
    font-size: 32px;
    color: var(--ink-soft);
    letter-spacing: 0.5px;
  }
  .edge-tab {
    position: absolute;
    left: 0;
    top: 160px;
    width: 21px;
    height: 81px;
    background: var(--brand-red);
    border-radius: 0 8px 8px 0;
  }
  .person-name {
    position: absolute;
    left: 64px;
    top: 172px;
    font-size: 31px;
    font-weight: 700;
    color: var(--brand-red);
  }
  .person-title {
    position: absolute;
    left: 64px;
    top: 215px;
    font-size: 23px;
    font-weight: 500;
    color: var(--ink-soft);
  }
  .address {
    position: absolute;
    left: 64px;
    top: 278px;
    font-size: 23px;
    line-height: 31px;
    font-style: normal;
    color: var(--ink-soft);
  }
  .contact-list {
    position: absolute;
    left: 70px;
    top: 356px;
    list-style: none;
  }
  .contact-item {
    display: flex;
    align-items: center;
    height: 32px;
    font-size: 23px;
    color: var(--ink-soft);
  }
  .contact-icon {
    width: 20px;
    height: 20px;
    margin-right: 14px;
    fill: var(--brand-red);
  }
  .brand-block {
    position: absolute;
    left: 451px;
    top: 22px;
    width: 523px;
    height: 541px;
    display: flex;
    align-items: center;
    justify-content: center;
  }
  .brand-word {
    font-family: "Cinzel", Georgia, serif;
    font-weight: 500;
    font-size: 60px;
    color: var(--brand-red);
  }
</style>
</head>
<body>
  <div class="business-card">
    <div class="company-name">Brindle Auto Ltd.</div>
    <div class="edge-tab"></div>

    <div class="person-name">MARK DALTON</div>
    <div class="person-title">CEO/FOUNDER</div>

    <address class="address">2140 Harlow Street<br>Fairbanks, Alaska 99701</address>

    <ul class="contact-list">
      <li class="contact-item">
        <svg class="contact-icon" viewBox="0 0 20 20" aria-hidden="true"><path d="M4 1l4 4-2 3c1 2 4 5 6 6l3-2 4 4-3 3C8 19 1 12 1 4z"/></svg>
        907 555 0142
      </li>
      <li class="contact-item">
        <svg class="contact-icon" viewBox="0 0 20 20" aria-hidden="true"><path d="M5 0h10a1 1 0 011 1v18a1 1 0 01-1 1H5a1 1 0 01-1-1V1a1 1 0 011-1zm1 3v11h8V3zm4 13a1.3 1.3 0 100 2.6A1.3 1.3 0 0010 16z" fill-rule="evenodd"/></svg>
        907 555 0187
      </li>
      <li class="contact-item">
        <svg class="contact-icon" viewBox="0 0 20 20" aria-hidden="true"><path d="M5 1h10v5H5zM1 7h18v8h-3v4H4v-4H1zm5 6v4h8v-4z" fill-rule="evenodd"/></svg>
        907 555 0163
      </li>
      <li class="contact-item">
        <svg class="contact-icon" viewBox="0 0 20 20" aria-hidden="true"><path d="M1 4h18v12H1zm1.5 1.5L10 11l7.5-5.5z" fill-rule="evenodd"/></svg>
        mark@brindleauto.com
      </li>
      <li class="contact-item">
        <svg class="contact-icon" viewBox="0 0 20 20" aria-hidden="true"><circle cx="10" cy="10" r="9"/><path d="M6 5c2 1 2 3 4 3s1 3-1 4-1 4-2 5M13 3c-1 2 1 3 3 3" stroke="#f1f0ee" stroke-width="1.5" fill="none"/></svg>
        www.brindleauto.com
      </li>
    </ul>

    <div class="brand-block">
      <span class="brand-word">Brindle Auto</span>
    </div>
  </div>
</body>
</html>
```